Web Design Project for a Software & Consulting Company

We have just completed a recent ArtHerdly project for a new logo (see attached).
As the next stage of our rebranding we now require a website re-design to complement the new logo.
Our current site, http://www.corvinsoft.example was built in-house and does not come across as professional as we would like. We supply software and associated services to some of the world’s largest oil companies and we need our site to reflect that level of client.
We will also be posting another design project for brochures, PowerPoint slides and other materials very soon.
We would like designs for…
Home page
Product page
• TZQ
• BLV
• PNJ
Services
News page
About Us page
Contact Us page
Page for mobile devices that gives basic company and product information
Currently the site is small but we intend to increase content to include white papers etc. this should be taken into account when designing the navigation therefore we would prefer navigation through styled text links rather than images.
Colour schemes should broadly be taken from our new logo, where the dark blue and dark green from the left and right sides of the logo are the main colours, but other, brighter accent colours can be used to highlight sections or content.
Dark Blue = C:88, M:55, Y:44, K:28
Dark Green = C:87, M:53, Y:50, K:50
NB: Don’t use the logo on our current site, make sure you use the one attached.
We would prefer the final file format to be a layered PSD.
The site should be clean and professional and communicate the following...
• That we have a great depth and breadth of knowledge about our customers’ business, enabling us to deliver the best systems and solutions.
• That we are a leading provider of cost estimation and control solutions to the oil and gas industry.
• The benefits of our software and consulting services.
• Show that we deliver outstanding customer service and value with a very high level of professionalism
• The site should have no Flash and be able to self-adjust to fit any screen size.
Things to avoid …
• Obvious and clichéd oil industry imagery, no oil rigs
• Cartoon style graphics
Our Background
We are an integrated software and consulting organization specialising in the drilling side of the oil and gas industry. Simply put our software helps companies better understand, predict and communicate the cost of drilling wells.
We have 3 software products and a consulting offering consisting of…
• TZQ - Probabilistic time and cost software
• BLV – Cost tracking and reporting software
• PNJ – (currently known as DrillSavant) – Lessons learned software
• Consulting services
Our systems are in use in over 30 countries with a broad range of clients including: GN, Marovel, Dunt, Koruna, VELO Sirkami, FALUMI and Quintex.
Our current site can be found at www.corvinsoft.example
Our main competitors are
• http://www.drovanic.example/
• http://www.sumbrask.example/
• http://www.kve.example/services/software-solutions/p1-
Our depth of drilling knowledge, quality of software and collaboration with clients differentiate us form the competition.
We strive for very high levels of customer service.
We look forward to receiving your designs!
Updates
Thanks to all the designers who have submitted a design, we appreciate the effort.
We will do our best to give individual feedback on each design but given that many are quite similar we thought we would give some general feedback first.
Nearly all the designs submitted so far have been slight variations on…
-
Top Menu
-
Scrolling Photo Banner
-
4 Columns
-
Body
-
Deep Footer
These designs are well executed but they are basically the same layout as our existing site and while there is nothing inherently wrong with this layout we would like to see some designs that are a bit more innovative and different. We don’t really want just a polished version of our current site.
Thanks again,
CVS
Thanks to everyone who has submitted a design, the response has been great.
We are close to making a decision so if you are intending to submit a design please do it soon, the deadline is only a few days away.
Thanks again.
CVS
Target Market(s)
Mid to high level executives
Industry/Entity Type
Oil And Gas
Look and feel

```html
<!DOCTYPE html>
<html lang="en">
<head>
<meta charset="utf-8">
<title>Contact Us – Corvin Software</title>
<link rel="stylesheet" href="https://fonts.googleapis.com/css2?family=Ubuntu:wght@400;500;700&family=Ubuntu+Condensed&family=Roboto+Condensed:wght@300;400&family=Arimo:ital@0;1&display=swap">
<style>
:root{
  --teal:#22566a;
  --teal-dark:#1a4556;
  --heading:#1e5266;
  --ink:#222;
  --muted:#555;
  --placeholder:#a8a8a8;
  --field-border:#cfcfcf;
  --green:#506c4e;
  --accent:#2aa6d6;
  --white:#fff;
}
*{box-sizing:border-box;margin:0;padding:0}
html,body{width:907px;height:1200px;overflow:hidden;background:var(--white)}
body{position:relative;font-family:"Arimo",Arial,sans-serif;color:var(--ink)}
.abs{position:absolute}

/* header */
.brand{left:112px;top:40px;display:flex;align-items:center;gap:8px}
.brand-mark{width:22px;height:22px;border-radius:50%;background:var(--teal)}
.brand-name{font-family:"Ubuntu",sans-serif;font-weight:700;font-size:17px;color:var(--teal);letter-spacing:.5px}
.nav{top:56px;font-family:"Ubuntu Condensed",sans-serif;font-size:12px;color:#111;letter-spacing:.2px}
.nav-active{left:743px;top:53px;width:72px;height:23px;background:var(--teal);border-radius:3px;color:var(--white);font-family:"Ubuntu Condensed",sans-serif;font-size:12px;text-align:center;line-height:23px}

/* banner */
.banner{left:90px;top:122px;width:725px;height:228px;background:linear-gradient(90deg,#f4f4f4 0%,#ececec 45%,#d9c2b1 62%,#c9a894 72%,#e9eee6 85%,#8cc24a 100%)}
.banner-band{left:90px;top:278px;width:725px;height:50px;background:rgba(26,75,94,.95)}
.banner-title{left:118px;top:290px;font-family:"Ubuntu",sans-serif;font-weight:700;font-size:21px;color:var(--white)}

/* form */
.form-icon{left:90px;top:380px}
.form-heading{left:134px;top:382px;font-family:"Ubuntu",sans-serif;font-size:18px;color:var(--heading)}
.intro{left:91px;top:436px;font-size:10px;color:#333}
.label{left:91px;font-family:"Roboto Condensed",sans-serif;font-weight:300;font-size:13px;color:#333}
.field{border:1px solid var(--field-border);border-radius:2px;background:linear-gradient(#f3f3f3,#fff 40%);font-style:italic;font-size:9px;color:var(--placeholder);padding:0 10px;line-height:27px}
.field-area{line-height:normal;padding-top:8px}
.check{display:flex;align-items:center;gap:8px;top:870px;font-size:10.5px;color:#1e3d5a}
.check-box{width:9px;height:9px;border:1px solid #888;background:#f5f5f5}
.hint{left:191px;top:893px;font-size:8.5px;font-style:italic;color:#444}
.submit{left:191px;top:929px;width:70px;height:26px;background:var(--green);color:var(--white);border-radius:2px;font-family:"Ubuntu Condensed",sans-serif;font-size:13px;text-align:center;line-height:26px}

/* footer */
.footer{left:90px;top:979px;width:725px;height:221px;background:var(--teal)}
.foot-head{top:996px;font-family:"Ubuntu Condensed",sans-serif;font-size:12px;color:var(--white)}
.foot-rule{height:1px;background:#6f97a6}
.foot-text{top:1019px;font-size:9.2px;line-height:12.8px;color:#e8f0f3}
.partner-badge{left:438px;top:1030px;width:160px;height:36px;border-radius:3px;background:#3a6c80}
.touch-head{left:641px;top:990px;font-family:"Ubuntu",sans-serif;font-size:15px;color:var(--white)}
.touch-rule{left:641px;top:1016px;width:131px;height:2px;background:linear-gradient(90deg,var(--accent),rgba(42,166,214,0))}
.touch-field{left:641px;width:150px;background:var(--white);border:1px solid #c8d4d8;font-size:9.5px;color:#222;padding:4px 8px}
.touch-submit{left:742px;top:1137px;width:49px;height:18px;background:linear-gradient(#fff,#ddd);border:1px solid #aaa;font-size:7.5px;text-align:center;line-height:16px;color:#111}
.foot-divider{left:110px;top:1090px;width:504px;height:1px;background:#5f8a9a}
.foot-lorem{left:110px;top:1100px;width:510px;font-size:9.3px;line-height:11px;color:#e8f0f3}
.foot-bar{left:90px;top:1170px;width:725px;height:1px;background:#174352}
.foot-links{left:110px;top:1180px;font-size:7.8px;color:#e8f0f3}
.copyright{right:116px;top:1180px;font-size:7.8px;color:#e8f0f3}
</style>
</head>
<body>

<header>
  <div class="abs brand"><span class="brand-mark"></span><span class="brand-name">CORVIN SOFTWARE</span></div>
  <nav>
    <span class="abs nav" style="left:404px">HOME</span>
    <span class="abs nav" style="left:466px">PRODUCTS</span>
    <span class="abs nav" style="left:547px">SERVICES</span>
    <span class="abs nav" style="left:622px">NEWS</span>
    <span class="abs nav" style="left:679px">ABOUT US</span>
    <span class="abs nav-active">CONTACT US</span>
  </nav>
</header>

<section>
  <div class="abs banner" role="img" aria-label="Photo of a smiling support agent wearing a headset beside a hand writing the words contact us"></div>
  <div class="abs banner-band"></div>
  <h1 class="abs banner-title">Contact Us</h1>
</section>

<main>
  <svg class="abs form-icon" width="30" height="30" viewBox="0 0 30 30" aria-hidden="true">
    <rect x="1" y="2" width="22" height="24" fill="#eef3f8" stroke="#6b8fb5"/>
    <rect x="1" y="2" width="22" height="4" fill="#4f7fb8"/>
    <line x1="4" y1="10" x2="18" y2="10" stroke="#9bb" />
    <line x1="4" y1="14" x2="16" y2="14" stroke="#9bb" />
    <line x1="4" y1="18" x2="14" y2="18" stroke="#9bb" />
    <circle cx="22" cy="20" r="3.5" fill="#e8b48a"/>
    <path d="M15 29 q7 -8 14 0z" fill="#e8761f"/>
  </svg>
  <h2 class="abs form-heading">Contact Corvin Software</h2>
  <p class="abs intro">Please complete the form below and we will get back to you as soon as possible.</p>

  <span class="abs label" style="top:478px">Name* :</span>
  <div class="abs field" style="left:192px;top:473px;width:235px;height:27px">Enter your first name...</div>
  <div class="abs field" style="left:446px;top:473px;width:235px;height:27px">Enter your first name...</div>

  <span class="abs label" style="top:528px">Email* :</span>
  <div class="abs field" style="left:192px;top:522px;width:489px;height:28px">Enter your email address...</div>

  <span class="abs label" style="top:577px">Phone Number :</span>
  <div class="abs field" style="left:192px;top:572px;width:489px;height:27px">Enter your phone number...</div>

  <span class="abs label" style="top:627px">Job Title&nbsp; :</span>
  <div class="abs field" style="left:192px;top:622px;width:489px;height:27px">Enter your job title...</div>

  <span class="abs label" style="top:676px">Company Name :</span>
  <div class="abs field" style="left:192px;top:670px;width:489px;height:28px">Enter your compnay name...</div>

  <span class="abs label" style="top:726px">Message :</span>
  <div class="abs field field-area" style="left:192px;top:721px;width:489px;height:118px">Enter your message...</div>

  <span class="abs label" style="top:869px">Software :</span>
  <label class="abs check" style="left:192px"><span class="check-box"></span>TZQ</label>
  <label class="abs check" style="left:262px"><span class="check-box"></span>BLV</label>
  <label class="abs check" style="left:331px"><span class="check-box"></span>DrillSavant</label>
  <p class="abs hint">If you are interested in our software please tick all relevant boxes on the left</p>

  <div class="abs submit">SUBMIT</div>
</main>

<footer>
  <div class="abs footer"></div>

  <h3 class="abs foot-head" style="left:113px">EUROPE</h3>
  <div class="abs foot-rule" style="left:113px;top:1014px;width:110px"></div>
  <p class="abs foot-text" style="left:112px">12 Harlow Crescent<br>Dunmere, DM4 2QT<br>Phone:+44(0)1632 960418<br>Email:eu@corvinsoft.example</p>

  <h3 class="abs foot-head" style="left:265px">NORTH AMERICA</h3>
  <div class="abs foot-rule" style="left:265px;top:1014px;width:110px"></div>
  <p class="abs foot-text" style="left:264px">4100 Larkspur Way, Suite 210<br>Brenford, TX 75010<br>Phone:(555) 014 2278<br>Email:us@corvinsoft.example</p>

  <h3 class="abs foot-head" style="left:433px">OUR GOLD BUSINESS PARTNER</h3>
  <div class="abs foot-rule" style="left:433px;top:1014px;width:169px"></div>
  <div class="abs partner-badge" role="img" aria-label="Gold partner badge"></div>

  <h3 class="abs touch-head">Get in touch</h3>
  <div class="abs touch-rule"></div>
  <div class="abs touch-field" style="top:1029px;height:19px">Name</div>
  <div class="abs touch-field" style="top:1055px;height:19px">E-mail</div>
  <div class="abs touch-field" style="top:1082px;height:47px">Message</div>
  <div class="abs touch-submit">SUBMIT</div>

  <div class="abs foot-divider"></div>
  <p class="abs foot-lorem">Lorem ipsum dolor sit amet, consectetur adipiscing elit. Donec semper nisl eget ante vehicula at viverra est porta. Morbi eleifend, turpis eget vehicula porta, leo velit facilisis justo, quis vehicula velit erat nec est. Pellentesque habitant morbi tristique senectus et netus et malesuada fames ac turpis egestas. Pellentesque consequat est vel metus luctus commodo. In hac habitasse platea dictumst. Suspendisse justo ipsum,</p>

  <div class="abs foot-bar"></div>
  <p class="abs foot-links">Privacy Policy &nbsp;|&nbsp; Terms &amp; Conditions</p>
  <p class="abs copyright">© Copyrights 2012 Corvin Software</p>
</footer>

</body>
</html>
```